Australian Trucking Company Requires Professional Looking Stationary

We require a professional looking stationary design that incorporates our newly designed logo.

Our business, called "Brell Haulage Contracting", provides contracting work, transport and logistics to business in Western Australia particularly with links to the mining sector.

We are a small business looking to expand and our new logo and our new stationary will help develop our brand image in our market place.

Target Market(s)

Businesses and Corporation with links to the Mining Sector

Industry/Entity Type

Small Business

Requirements
Must have
• The letterhead must have the following details:
The new logo

Text saying: "Brell Holdings Pty Ltd (ACN 582 316 907) ATF The Brell Discretionary Trust T/AS"
"ABN 71 834 209 553"
Address "P.O Box 817 Wattlegrove WA, 6958"
Phone: 08 9352 7140
Email: brellhaul@mailbox-example.com.au

The text on the letterhead should be editable as the details are likely to change in the near future. Provision should be made for a website address all though one isn't available at the moment.

The styling, layout and font text is entirely up to the designer.

```html
<!DOCTYPE html>
<html lang="en">
<head>
<meta charset="utf-8">
<title>Brell Haulage Contracting – Business Card</title>
<link rel="stylesheet" href="https://fonts.googleapis.com/css2?family=Open+Sans:wght@400;600;700;800&display=swap">
<style>
  :root {
    --stage: #e9e6e2;
    --card-white: #f7f7f7;
    --card-grey: #e6e6e6;
    --brand-red: #c4161c;
    --brand-red-dark: #8e0b10;
    --brand-red-deep: #6a0609;
    --band-grey: #3c3c3c;
    --band-grey-light: #6b6b6b;
    --ink: #2a2a2a;
    --white: #ffffff;
  }
  * { margin: 0; padding: 0; box-sizing: border-box; }
  html, body { width: 1200px; height: 426px; overflow: hidden; }
  body {
    background: var(--stage);
    font-family: "Open Sans", Arial, sans-serif;
    color: var(--ink);
    position: relative;
  }
  .card {
    position: absolute;
    border-radius: 22px;
    overflow: hidden;
    box-shadow: 0 4px 10px rgba(0,0,0,0.18);
  }
  .card--front {
    left: 52px; top: 48px; width: 520px; height: 300px;
    background: linear-gradient(180deg, var(--white) 0%, var(--card-white) 55%, var(--card-grey) 100%);
  }
  .card--back {
    left: 610px; top: 54px; width: 542px; height: 296px;
    background: radial-gradient(circle at 55% 45%, #e2262c 0%, var(--brand-red) 35%, var(--brand-red-dark) 75%, var(--brand-red-deep) 100%);
  }

  .brand-name {
    position: absolute;
    left: 158px; top: 30px;
    font-weight: 800;
    font-size: 27px;
    line-height: 28px;
    letter-spacing: 1px;
    text-transform: uppercase;
    color: var(--brand-red);
  }
  .brand-mark {
    position: absolute;
    left: 40px; top: 36px;
    width: 78px; height: 78px;
    border-radius: 50%;
    background: var(--brand-red);
  }

  .contact-list {
    position: absolute;
    left: 42px; top: 144px;
    list-style: none;
    font-size: 11.5px;
    line-height: 20px;
  }
  .contact-list li { display: flex; align-items: center; gap: 5px; }
  .contact-list svg { width: 10px; height: 10px; fill: var(--ink); }

  .company-details {
    position: absolute;
    left: 280px; top: 144px; width: 220px;
    text-align: center;
    font-size: 10.8px;
    line-height: 17px;
  }
  .company-details .web {
    display: flex; align-items: center; justify-content: center; gap: 4px;
    font-size: 11.5px; margin-bottom: 8px;
  }
  .company-details .web svg { width: 10px; height: 10px; }

  .band {
    position: absolute;
    left: 0; bottom: 0; width: 520px; height: 95px;
  }
  .holder {
    position: absolute;
    left: 40px; top: 240px;
    color: var(--white);
  }
  .holder-name { font-size: 17px; font-weight: 700; line-height: 22px; }
  .holder-role { font-size: 11px; margin-left: 44px; }

  .back-name {
    position: absolute;
    left: 0; right: 0; top: 112px;
    text-align: center;
    font-weight: 800;
    font-size: 30px;
    line-height: 36px;
    letter-spacing: 1px;
    text-transform: uppercase;
    color: var(--white);
  }
</style>
</head>
<body>

<section class="card card--front" aria-label="Business card front">
  <span class="brand-mark" aria-hidden="true"></span>
  <div class="brand-name">Brell<br>Haulage<br>Contracting</div>

  <ul class="contact-list">
    <li>
      <svg viewBox="0 0 10 10" aria-hidden="true"><path d="M2 0.5 L3.6 2.6 L2.8 3.6 Q4 6 6.4 7.2 L7.4 6.4 L9.5 8 L8.4 9.5 Q3.5 9 0.5 1.6 Z"/></svg>
      08 9352 7140
    </li>
    <li>
      <svg viewBox="0 0 10 10" aria-hidden="true"><path d="M0.5 2 H9.5 V8 H0.5 Z M1.2 2.6 L5 5.4 L8.8 2.6" fill="none" stroke="#2a2a2a" stroke-width="1"/></svg>
      brellhaul@mailbox-example.com.au
    </li>
    <li>
      <svg viewBox="0 0 10 10" aria-hidden="true"><path d="M5 0.8 L9.6 5 H8.2 V9.4 H6 V6.6 H4 V9.4 H1.8 V5 H0.4 Z"/></svg>
      P.O Box 817 Wattlegrove WA, 6958
    </li>
  </ul>

  <div class="company-details">
    <div class="web">
      <svg viewBox="0 0 10 10" aria-hidden="true"><circle cx="5" cy="5" r="4.3" fill="none" stroke="#c4161c" stroke-width="1"/><path d="M0.8 5 H9.2 M5 0.7 Q2.4 5 5 9.3 M5 0.7 Q7.6 5 5 9.3" fill="none" stroke="#c4161c" stroke-width="0.8"/></svg>
      www.brellhaulage-example.com
    </div>
    <p>Brell Holdings Pty Ltd (ACN 582 316 907)</p>
    <p>ATF The Brell Discretionary Trust T/AS</p>
    <p>ABN 71 834 209 553</p>
  </div>

  <svg class="band" viewBox="0 0 520 95" preserveAspectRatio="none" aria-hidden="true">
    <defs>
      <linearGradient id="band-red" x1="0" y1="0" x2="1" y2="0">
        <stop offset="0" stop-color="#8e0b10"/>
        <stop offset="0.45" stop-color="#c4161c"/>
        <stop offset="1" stop-color="#a10f14"/>
      </linearGradient>
      <linearGradient id="band-grey" x1="0" y1="0" x2="1" y2="0">
        <stop offset="0" stop-color="#6b6b6b"/>
        <stop offset="1" stop-color="#2e2e2e"/>
      </linearGradient>
    </defs>
    <path d="M0 10 Q120 -8 230 30 Q330 62 520 40 V95 H0 Z" fill="url(#band-grey)"/>
    <path d="M0 10 Q120 -8 220 30 Q270 50 300 70 Q250 95 200 95 H0 Z" fill="url(#band-red)"/>
  </svg>

  <div class="holder">
    <div class="holder-name">Persons name</div>
    <div class="holder-role">Manager</div>
  </div>
</section>

<section class="card card--back" aria-label="Business card back">
  <div class="back-name">Brell<br>Haulage Contracting</div>
</section>

</body>
</html>
```